Threat Lens ratings for Apps and Games

I need a web site designing that is aimed at parents and will show an "Threat Lens" rating for apps and games. I have attached a document with an overview of what the Threat Lens is. The website needs to be easy for parents to navigate and find what they want quickly and easily. I should also be able to update the website myself easily with "reviews" of the attack vectors for apps and games.

Target Market(s)

Parents

Coding

Coded - Design and coding required

Number of Pages Required

2 page

Requirements
Must have
• Clear and concise ratings for apps and games

```html
<!DOCTYPE html>
<html lang="en">
<head>
<meta charset="utf-8">
<title>Threat Lens – App &amp; Game Ratings for Parents</title>
<link href="https://fonts.googleapis.com/css2?family=Roboto:ital,wght@0,400;0,500;0,700;0,900;1,400&family=Lora:ital@1&display=swap" rel="stylesheet">
<style>
:root{
  --blue:#1b46a9;
  --blue-dark:#163c93;
  --lavender:#dfe2f9;
  --lavender-soft:#eef0fc;
  --ink:#111;
  --text:#5d5d5d;
  --muted:#8a8a8a;
  --footer:#121212;
  --footer-text:#d8d8d8;
  --gold:#f5b800;
  --white:#fff;
}
*{box-sizing:border-box;margin:0;padding:0}
html,body{width:1200px;height:4239px;overflow:hidden}
body{font-family:"Roboto",Arial,sans-serif;color:var(--ink);background:var(--white);position:relative}
a{color:inherit;text-decoration:none}
.abs{position:absolute}

/* Header / hero */
.hero{position:absolute;left:0;top:0;width:1200px;height:617px}
.hero-blob{position:absolute;left:0;top:0}
.brand{position:absolute;left:112px;top:14px;display:flex;flex-direction:column;align-items:center;gap:8px}
.brand-dot{width:50px;height:50px;border-radius:50%;background:var(--blue)}
.brand-name{font-size:42px;font-weight:500;letter-spacing:.5px;line-height:1}
.nav{position:absolute;top:57px;left:0;font-size:18px;font-weight:500}
.nav a{position:absolute;white-space:nowrap}
.top-mail{position:absolute;left:766px;top:14px;font-size:17px;display:flex;align-items:center;gap:7px}
.btn{display:inline-flex;align-items:center;justify-content:center;background:var(--blue);color:var(--white);font-weight:700;border-radius:23px;text-transform:uppercase;letter-spacing:.2px}
.btn-login{position:absolute;left:988px;top:8px;width:98px;height:33px;font-size:16px;font-weight:500}
.hero-art{position:absolute;left:584px;top:92px;width:500px;height:470px;border-radius:40% 45% 42% 38%;background:radial-gradient(ellipse at 50% 60%,#b9bff0 0%,#cfd3f6 45%,rgba(223,226,249,0) 72%)}
.hero-title{position:absolute;left:112px;top:243px;font-size:51px;font-weight:900;letter-spacing:.5px}
.hero-lead{position:absolute;left:112px;top:311px;width:490px;font-size:16.5px;font-weight:500;line-height:29px}
.btn-start{position:absolute;left:112px;top:416px;width:162px;height:45px;font-size:16px}

/* Features */
.section-title{position:absolute;left:0;width:1200px;text-align:center;font-size:39px;font-weight:700;letter-spacing:.3px}
.feature{position:absolute;left:0;width:1200px;height:405px}
.feature-art{position:absolute;border-radius:18px}
.feature-title{position:absolute;font-size:24px;font-weight:500;color:var(--blue);text-transform:uppercase;letter-spacing:.3px}
.feature-text{position:absolute;width:450px;font-size:13.4px;line-height:28.3px;color:var(--text)}
.btn-more{position:absolute;width:162px;height:45px;font-size:16px}

/* FAQ */
.faq{position:absolute;left:0;top:2810px;width:1200px;height:559px}
.faq-side{position:absolute;left:0;top:0;width:599px;height:559px;background:var(--lavender-soft)}
.faq-art{position:absolute;left:41px;top:87px;width:510px;height:362px;border-radius:46% 40% 12% 12%;background:linear-gradient(160deg,#d2d7f7 0%,#c3caf3 55%,#e8a08f 78%,#cfd5f6 100%)}
.faq-main{position:absolute;left:599px;top:0;width:601px;height:559px;background:var(--blue)}
.faq-title{position:absolute;left:35px;top:60px;font-size:26px;font-weight:700;color:var(--white)}
.faq-item{position:absolute;left:36px;width:499px;height:61px;background:var(--white);display:flex;align-items:center;padding:0 42px 0 14px;font-size:12.8px;line-height:17px;color:#555}
.faq-item::after{content:"";position:absolute;right:16px;top:50%;width:18px;height:18px;margin-top:-9px;background:
  linear-gradient(var(--blue),var(--blue)) center/18px 1.6px no-repeat,
  linear-gradient(var(--blue),var(--blue)) center/1.6px 18px no-repeat}
.faq-more{position:absolute;left:284px;top:484px}

/* Testimonials */
.review{position:absolute;top:3517px;width:291px;height:272px;background:var(--white);box-shadow:0 0 14px rgba(0,0,0,.08)}
.review-avatar{position:absolute;left:16px;top:36px;width:44px;height:44px;border-radius:50%;background:linear-gradient(135deg,#9a8a7c,#d8d0c6)}
.review-name{position:absolute;left:75px;top:47px;font-size:18px;font-weight:500}
.review-text{position:absolute;left:16px;top:92px;width:262px;font-family:"Lora",Georgia,serif;font-style:italic;font-size:15px;line-height:28.5px;color:#333}
.review-stars{position:absolute;left:16px;top:214px;font-size:24px;letter-spacing:1px;color:var(--gold)}
.review-quote{position:absolute;right:18px;top:190px;font-family:Georgia,serif;font-size:130px;line-height:1;color:#c9c9c9;font-weight:700}
.slider-arrow{position:absolute;top:3804px}

/* Footer */
.footer{position:absolute;left:0;top:3882px;width:1200px;height:357px;background:var(--footer);color:var(--footer-text)}
.footer-brand{position:absolute;left:112px;top:100px;display:flex;flex-direction:column;align-items:center;gap:10px}
.footer-brand .brand-dot{width:44px;height:44px;background:var(--white)}
.footer-brand .brand-name{font-size:30px;color:var(--white)}
.social{position:absolute;top:196px;width:33px;height:33px;border:1.5px solid var(--white);border-radius:50%}
.footer-col h4{position:absolute;font-size:17px;font-weight:500;color:var(--white)}
.footer-col a,.footer-col p{position:absolute;font-size:14.5px;line-height:24px;white-space:nowrap}
.contact-icon{position:absolute}
.footer-rule{position:absolute;left:112px;top:299px;width:976px;height:1px;background:#555}
.copyright{position:absolute;left:0;top:318px;width:1200px;text-align:center;font-size:13px;color:var(--white)}
</style>
</head>
<body>

<header class="hero">
  <svg class="hero-blob" width="1200" height="617" viewBox="0 0 1200 617" aria-hidden="true">
    <path d="M590 0 H1200 V617 H760 C720 590 720 560 690 548 C640 530 600 470 560 420 C520 360 520 300 560 250 C600 200 520 160 500 110 C480 60 530 20 590 0 Z" fill="var(--lavender)"/>
  </svg>
  <div class="brand">
    <span class="brand-dot"></span>
    <span class="brand-name">THREAT LENS</span>
  </div>
  <nav class="nav">
    <a href="#" style="left:504px">About Us</a>
    <a href="#" style="left:642px">Features</a>
    <a href="#" style="left:779px">Faq</a>
    <a href="#" style="left:874px">Review</a>
    <a href="#" style="left:999px">Contact Us</a>
  </nav>
  <div class="top-mail">
    <svg width="16" height="12" viewBox="0 0 16 12" aria-hidden="true"><rect width="16" height="12" rx="1.5" fill="var(--blue)"/><path d="M1 1.5 8 7 15 1.5" stroke="#fff" stroke-width="1.4" fill="none"/></svg>
    info@threatlens.example
  </div>
  <a class="btn btn-login" href="#">LOGIN</a>
  <div class="hero-art" role="img" aria-label="Illustration of a family relaxing on a sofa with phones, a laptop and a tablet"></div>
  <h1 class="hero-title">THREAT LENS</h1>
  <p class="hero-lead">Lorem ipsum dolor sit amet, consectetur adipiscing elit, sed do eiusmod tempor incididunt ut labore et dolore Lorem ipsum dolor sit amet, consectetur adipiscing elit,</p>
  <a class="btn btn-start" href="#">GET STARTED</a>
</header>

<main>
  <h2 class="section-title" style="top:712px">OUR FEATURES</h2>

  <section class="feature" style="top:801px">
    <div class="feature-art" role="img" aria-label="Illustration of two people beside a large phone showing a login form" style="left:173px;top:0;width:362px;height:318px;background:linear-gradient(160deg,#f1f3f8,#dfe6f7 60%,#5b93e8)"></div>
    <h3 class="feature-title" style="left:601px;top:21px">LOGIN</h3>
    <p class="feature-text" style="left:601px;top:65px">Lorem ipsum dolor sit amet, consectetur adipiscing elit, sed do ed tempor incididunt ut re et dolore magna aliqua. Quis ipsum ssse ultrices gravida. Risus commodo viverra maecenas accumsal facilisis. Lorem ipsum dolor sit amet, consectetur adipiscing elit, sed do eiusmod tempor incididunt ut re et dolore magna aliqua. Quis ipsum suspendisse ultrices gravida. Risus commodo viverra maecenas accumsan lacus vel facilisis.</p>
    <a class="btn btn-more" href="#" style="left:602px;top:257px">LEARN MORE</a>
  </section>

  <section class="feature" style="top:1206px">
    <div class="feature-art" role="img" aria-label="Illustration of people beside a phone showing chat bubbles" style="left:650px;top:7px;width:325px;height:285px;background:linear-gradient(160deg,#f3f4f7,#e3ebfb 55%,#4f8be6)"></div>
    <h3 class="feature-title" style="left:148px;top:21px">CHAT/MESSAGING</h3>
    <p class="feature-text" style="left:148px;top:65px">Lorem ipsum dolor sit amet, consectetur adipiscing elit, sed do ed tempor incididunt ut re et dolore magna aliqua. Quis ipsum ssse ultrices gravida. Risus commodo viverra maecenas accumsal facilisis. Lorem ipsum dolor sit amet, consectetur adipiscing elit, sed do eiusmod tempor incididunt ut re et dolore magna aliqua. Quis ipsum suspendisse ultrices gravida. Risus commodo viverra maecenas accumsan lacus vel facilisis.</p>
    <a class="btn btn-more" href="#" style="left:150px;top:257px">LEARN MORE</a>
  </section>

  <section class="feature" style="top:1611px">
    <div class="feature-art" role="img" aria-label="Illustration of two phones on a video call with people around them" style="left:107px;top:76px;width:456px;height:185px;background:linear-gradient(90deg,#f6d9b5,#e8edf8 35%,#d6e4fb 65%,#f2c98e)"></div>
    <h3 class="feature-title" style="left:601px;top:21px">CAMERA/MICROPHONE ACCESS</h3>
    <p class="feature-text" style="left:601px;top:65px">Lorem ipsum dolor sit amet, consectetur adipiscing elit, sed do ed tempor incididunt ut re et dolore magna aliqua. Quis ipsum ssse ultrices gravida. Risus commodo viverra maecenas accumsal facilisis. Lorem ipsum dolor sit amet, consectetur adipiscing elit, sed do eiusmod tempor incididunt ut re et dolore magna aliqua. Quis ipsum suspendisse ultrices gravida. Risus commodo viverra maecenas accumsan lacus vel facilisis.</p>
    <a class="btn btn-more" href="#" style="left:602px;top:259px">LEARN MORE</a>
  </section>

  <section class="feature" style="top:2018px">
    <div class="feature-art" role="img" aria-label="Illustration of a phone showing a map with location pins, a cyclist and a walker" style="left:630px;top:-13px;width:390px;height:296px;background:linear-gradient(150deg,#7fb07a,#e6ebf4 35%,#d9e2f3 65%,#f49a4b)"></div>
    <h3 class="feature-title" style="left:148px;top:21px">LOCATION SERVICES</h3>
    <p class="feature-text" style="left:148px;top:65px">Lorem ipsum dolor sit amet, consectetur adipiscing elit, sed do ed tempor incididunt ut re et dolore magna aliqua. Quis ipsum ssse ultrices gravida. Risus commodo viverra maecenas accumsal facilisis. Lorem ipsum dolor sit amet, consectetur adipiscing elit, sed do eiusmod tempor incididunt ut re et dolore magna aliqua. Quis ipsum suspendisse ultrices gravida. Risus commodo viverra maecenas accumsan lacus vel facilisis.</p>
    <a class="btn btn-more" href="#" style="left:150px;top:257px">LEARN MORE</a>
  </section>

  <section class="feature" style="top:2423px">
    <div class="feature-art" role="img" aria-label="Illustration of a person with headphones live streaming from a laptop with chat messages" style="left:173px;top:46px;width:317px;height:293px;background:linear-gradient(160deg,#e9eef6,#c9dcf4 50%,#6f9fd8)"></div>
    <h3 class="feature-title" style="left:601px;top:21px">LIVE STREAMING</h3>
    <p class="feature-text" style="left:601px;top:65px">Lorem ipsum dolor sit amet, consectetur adipiscing elit, sed do ed tempor incididunt ut re et dolore magna aliqua. Quis ipsum ssse ultrices gravida. Risus commodo viverra maecenas accumsal facilisis. Lorem ipsum dolor sit amet, consectetur adipiscing elit, sed do eiusmod tempor incididunt ut re et dolore magna aliqua. Quis ipsum suspendisse ultrices gravida. Risus commodo viverra maecenas accumsan lacus vel facilisis.</p>
    <a class="btn btn-more" href="#" style="left:602px;top:257px">LEARN MORE</a>
  </section>

  <section class="faq">
    <div class="faq-side">
      <div class="faq-art" role="img" aria-label="Illustration of a family on a sofa using phones, a laptop and a tablet under a wifi signal"></div>
    </div>
    <div class="faq-main">
      <h2 class="faq-title">FREQUENTLY ASKED QUESTIONS</h2>
      <div class="faq-item" style="top:113px">Does the game or app have access to the camera and mic and does the game/app have the ability to send pics or video within the app itself ?</div>
      <div class="faq-item" style="top:184px">Does the game or app have voice chat and can voice changing software interface into the game or app ?</div>
      <div class="faq-item" style="top:255px">Does the game or app have an inbuilt messaging service and what types of messages and content can be sent over this ?</div>
      <div class="faq-item" style="top:325px">Does it have any constraints on username such as length or whether you can use profanity on the user name ?</div>
      <div class="faq-item" style="top:395px">What are the password requirements in terms of length, complexity, does it allow you to use a recently used password ?</div>
      <svg class="faq-more" width="30" height="16" viewBox="0 0 30 16" aria-hidden="true"><path d="M2 2 15 14 28 2" stroke="#fff" stroke-width="2.2" fill="none"/></svg>
    </div>
  </section>

  <h2 class="section-title" style="top:3441px">CLIENTS ABOUT US</h2>

  <article class="review" style="left:145px">
    <div class="review-avatar" role="img" aria-label="Reviewer portrait photo"></div>
    <h3 class="review-name">Mara in Elmwood</h3>
    <p class="review-text">Theo is an absolute gem. I feel lucky to have him working on my garden. He is a very hard worker and gives 120%. Can recommend him to anyone.</p>
    <div class="review-stars">★★★★★</div>
    <div class="review-quote">”</div>
  </article>
  <article class="review" style="left:454px">
    <div class="review-avatar" role="img" aria-label="Reviewer portrait photo"></div>
    <h3 class="review-name">Owen Hale</h3>
    <p class="review-text">Lorem ipsum dolor sit amet, consectetur adipiscing elit, sed do eiusmod tempor incididunt ut labore et dolore magna aliqua. Quis ipsum</p>
    <div class="review-stars">★★★★★</div>
    <div class="review-quote">”</div>
  </article>
  <article class="review" style="left:764px">
    <div class="review-avatar" role="img" aria-label="Reviewer portrait photo"></div>
    <h3 class="review-name">Owen Hale</h3>
    <p class="review-text">Lorem ipsum dolor sit amet, consectetur adipiscing elit, sed do eiusmod tempor incididunt ut labore et dolore magna aliqua. Quis ipsum</p>
    <div class="review-stars">★★★★★</div>
    <div class="review-quote">”</div>
  </article>
  <svg class="slider-arrow" style="left:146px" width="20" height="12" viewBox="0 0 20 12" aria-hidden="true"><path d="M19 6H2M7 1 2 6l5 5" stroke="#888" stroke-width="1.4" fill="none"/></svg>
  <svg class="slider-arrow" style="left:1034px" width="20" height="12" viewBox="0 0 20 12" aria-hidden="true"><path d="M1 6h17M13 1l5 5-5 5" stroke="#888" stroke-width="1.4" fill="none"/></svg>
</main>

<footer class="footer">
  <div class="footer-brand">
    <span class="brand-dot"></span>
    <span class="brand-name">THREAT LENS</span>
  </div>
  <span class="social" style="left:142px"></span>
  <span class="social" style="left:183px"></span>
  <span class="social" style="left:224px"></span>
  <span class="social" style="left:265px"></span>

  <div class="footer-col">
    <h4 style="left:395px;top:84px">Contact US</h4>
    <svg class="contact-icon" style="left:398px;top:124px" width="10" height="14" viewBox="0 0 10 14" aria-hidden="true"><path d="M5 0C2.2 0 0 2.2 0 5c0 3.5 5 9 5 9s5-5.5 5-9c0-2.8-2.2-5-5-5zm0 7a2 2 0 1 1 0-4 2 2 0 0 1 0 4z" fill="#fff"/></svg>
    <p style="left:417px;top:116px">123 Avenue name, City<br>name 10150, United States</p>
    <svg class="contact-icon" style="left:397px;top:193px" width="12" height="12" viewBox="0 0 12 12" aria-hidden="true"><path d="M2.5.5 4.5 3 3.3 4.5a7 7 0 0 0 4.2 4.2L9 7.5l2.5 2-1.2 2C5.5 11.5.5 6.5.5 1.7z" fill="#fff"/></svg>
    <p style="left:417px;top:187px">(888) 888-8888</p>
    <svg class="contact-icon" style="left:396px;top:237px" width="13" height="10" viewBox="0 0 13 10" aria-hidden="true"><rect x=".6" y=".6" width="11.8" height="8.8" fill="none" stroke="#fff" stroke-width="1.2"/><path d="M1 1 6.5 5.5 12 1" stroke="#fff" stroke-width="1.2" fill="none"/></svg>
    <p style="left:420px;top:231px">info@threatlens.example</p>
  </div>

  <div class="footer-col">
    <h4 style="left:655px;top:84px">Quick Links</h4>
    <a href="#" style="left:655px;top:123px">About Us</a>
    <a href="#" style="left:655px;top:155px">Features</a>
    <a href="#" style="left:658px;top:186px">Faq</a>
    <a href="#" style="left:655px;top:219px">Review</a>
  </div>
  <div class="footer-col">
    <h4 style="left:810px;top:84px">Get Help</h4>
    <a href="#" style="left:810px;top:123px">Contact Us</a>
    <a href="#" style="left:810px;top:155px">Media</a>
  </div>
  <div class="footer-col">
    <h4 style="left:945px;top:84px">Legal</h4>
    <a href="#" style="left:945px;top:123px">Terms and Conditions</a>
    <a href="#" style="left:945px;top:155px">Cookies</a>
    <a href="#" style="left:945px;top:186px">Privacy Policy</a>
  </div>

  <div class="footer-rule"></div>
  <p class="copyright">© 2021 Threat Lens. All Rights Reserved.</p>
</footer>

</body>
</html>
```